Cedar Brook Stables, LLC

Equestrian business card to promote equine retirement, farm sitting, short term board. Located in Aiken, SC.
Updates
Updated color schemes.
Contact Information for Business Card
Contact info, description of work.
Colors
0094D4
00A9DD
6FCCEA
C7EBF8
E9F6FB
59FF00
82FF00
B8FF75
E3FFCB
F4FFEA
F0912C
F2A743
F7CA91
FBE8D2
FDF5EE

```html
<!DOCTYPE html>
<html lang="en">
<head>
<meta charset="utf-8">
<title>Cedar Brook Stables – Business Card</title>
<link rel="stylesheet" href="https://fonts.googleapis.com/css2?family=Montserrat:wght@500;600;700&family=Poppins:wght@400;500&display=swap">
<style>
  :root {
    --backdrop: #c9c9c9;
    --brand-green: #0f7a0c;
    --brand-green-deep: #0b6a09;
    --deco-green: #1f8a14;
    --accent-gold: #f5c518;
    --card-white: #ffffff;
    --ink-dark: #2f2f2f;
    --ink-mid: #3a3a3a;
    --deco-soft: #fbf3dc;
    --deco-ring: #e6f1e3;
  }
  * { box-sizing: border-box; margin: 0; padding: 0; }
  html, body { width: 1200px; height: 900px; overflow: hidden; }
  body {
    background: var(--backdrop);
    font-family: "Poppins", sans-serif;
    position: relative;
  }
  .card {
    position: absolute;
    width: 680px;
    height: 390px;
    border-radius: 28px;
    overflow: hidden;
    box-shadow: 0 12px 28px rgba(0,0,0,0.25);
  }

  /* Front side */
  .card--front {
    left: 60px; top: 50px;
    background: var(--brand-green);
    color: var(--card-white);
  }
  .front-emblem {
    position: absolute;
    right: 40px; top: 20px;
    width: 350px; height: 350px;
    border-radius: 50%;
    background: radial-gradient(circle at 50% 60%, var(--deco-green) 0%, var(--brand-green-deep) 70%, var(--brand-green) 100%);
    opacity: 0.8;
  }
  .front-title {
    position: absolute;
    left: 0; right: 0; top: 150px;
    text-align: center;
    font-family: "Montserrat", sans-serif;
    font-weight: 700;
    font-size: 46px;
    letter-spacing: 3px;
  }
  .front-services {
    position: absolute;
    left: 0; right: 0; top: 250px;
    text-align: center;
    font-family: "Montserrat", sans-serif;
    font-weight: 600;
    font-size: 16px;
    letter-spacing: 1.5px;
  }
  .service-dot {
    display: inline-block;
    width: 9px; height: 9px;
    border-radius: 50%;
    background: var(--accent-gold);
    margin: 0 10px;
    vertical-align: middle;
  }

  /* Back side */
  .card--back {
    left: 460px; top: 460px;
    background: var(--card-white);
    color: var(--ink-dark);
  }
  .back-emblem {
    position: absolute;
    right: -30px; top: 10px;
    width: 400px; height: 400px;
    border-radius: 50%;
    border: 10px solid var(--deco-ring);
    background: radial-gradient(circle at 50% 60%, var(--deco-soft) 0%, #fdfaf0 60%, var(--card-white) 100%);
  }
  .brand-mark {
    position: absolute;
    left: 40px; top: 90px;
    display: flex;
    align-items: center;
    gap: 12px;
  }
  .brand-dot {
    width: 22px; height: 22px;
    border-radius: 50%;
    background: var(--brand-green);
  }
  .brand-name {
    font-family: "Montserrat", sans-serif;
    font-weight: 700;
    font-size: 26px;
    letter-spacing: 1px;
    color: var(--ink-dark);
    line-height: 1.15;
  }
  .contact-list {
    position: absolute;
    left: 40px; top: 240px;
    list-style: none;
    font-size: 19px;
    color: var(--ink-dark);
  }
  .contact-list li {
    display: flex;
    align-items: center;
    gap: 12px;
    line-height: 1.55;
  }
  .contact-list svg { width: 18px; height: 18px; flex: none; }
  .web-name { color: var(--brand-green); }
  .person {
    position: absolute;
    right: 40px; top: 120px;
    text-align: right;
  }
  .person-name {
    font-family: "Montserrat", sans-serif;
    font-weight: 700;
    font-size: 28px;
    color: var(--brand-green);
    letter-spacing: 1px;
  }
  .person-role {
    font-family: "Montserrat", sans-serif;
    font-weight: 500;
    font-size: 18px;
    color: var(--ink-mid);
  }
  .address {
    position: absolute;
    right: 40px; top: 230px;
    text-align: right;
    font-family: "Montserrat", sans-serif;
    font-weight: 500;
    font-size: 17px;
    line-height: 1.5;
    color: var(--ink-mid);
  }
</style>
</head>
<body>

<section class="card card--front" aria-label="Business card front">
  <div class="front-emblem" role="img" aria-label="Faint brand emblem area"></div>
  <h1 class="front-title">CEDAR BROOK STABLES</h1>
  <p class="front-services">SHORT TERM BOARD<span class="service-dot"></span>FARM SITTING<span class="service-dot"></span>EQUINE RETIREMENT</p>
</section>

<section class="card card--back" aria-label="Business card back">
  <div class="back-emblem" role="img" aria-label="Faint brand emblem area"></div>

  <div class="brand-mark">
    <span class="brand-dot"></span>
    <span class="brand-name">CEDAR BROOK<br>STABLES, LLC</span>
  </div>

  <ul class="contact-list">
    <li>
      <svg viewBox="0 0 24 24" fill="var(--brand-green)" aria-hidden="true"><path d="M6.6 10.8a15 15 0 0 0 6.6 6.6l2.2-2.2a1 1 0 0 1 1-.25 11.4 11.4 0 0 0 3.6.57 1 1 0 0 1 1 1V20a1 1 0 0 1-1 1A17 17 0 0 1 3 4a1 1 0 0 1 1-1h3.5a1 1 0 0 1 1 1c0 1.25.2 2.45.57 3.6a1 1 0 0 1-.25 1z"/></svg>
      044-555 010 246
    </li>
    <li>
      <svg viewBox="0 0 24 24" fill="var(--brand-green)" aria-hidden="true"><path d="M2 5h20v14H2z M4 7v.5l8 5 8-5V7l-8 5z" fill-rule="evenodd"/></svg>
      hello@cedarbrook.com
    </li>
    <li>
      <svg viewBox="0 0 24 24" fill="none" stroke="var(--brand-green)" stroke-width="2" aria-hidden="true"><circle cx="12" cy="12" r="9"/><path d="M3 12h18M12 3c3 3 3 15 0 18M12 3c-3 3-3 15 0 18"/></svg>
      <span>www.<span class="web-name">cedarbrookstables</span>.com</span>
    </li>
  </ul>

  <div class="person">
    <p class="person-name">DANIEL HARPER</p>
    <p class="person-role">Managing Director</p>
  </div>

  <p class="address">118 Stable Lane, Aiken<br>SC 29801, United States</p>
</section>

</body>
</html>
```